Vision, Mission and Culture Posters

We have written text paragraphs for our company vision and mission and need them made into a2 or a3 sized posters using our logo for inspiration for colour. Our company culture has 10 paragraphs and we'd like this to be a single poster of a2 or a1. Each poster should have the logo on and share common design. It's not a complex job really.

Industry/Entity Type

It Company

Requirements
Nice to have
• These will be going up on our office wall so need to be clear to read from a distance and look professional but also not stodgy.

```html
<!DOCTYPE html>
<html lang="en">
<head>
<meta charset="utf-8">
<title>Kerbside Spaces – Mission Poster</title>
<link rel="stylesheet" href="https://fonts.googleapis.com/css2?family=Open+Sans:ital,wght@0,400;0,700;1,700&display=swap">
<style>
  :root {
    --paper: #f2f2f4;
    --ink: #3a3a3c;
    --red: #ec4034;
    --brand-yellow: #e8e21e;
    --olive: #b4b21b;
    --gold: #e3cf1d;
    --orange: #ef6a27;
  }
  * { margin: 0; padding: 0; box-sizing: border-box; }
  html, body { width: 848px; height: 1200px; overflow: hidden; background: var(--paper); }
  .poster {
    position: relative;
    width: 848px;
    height: 1200px;
    background: var(--paper);
    font-family: "Open Sans", "Myriad Pro", sans-serif;
    color: var(--ink);
    overflow: hidden;
  }
  .brand {
    position: absolute;
    left: 130px;
    top: 62px;
    width: 580px;
    height: 100px;
    display: flex;
    align-items: center;
    justify-content: center;
    gap: 22px;
  }
  .brand-square {
    width: 46px;
    height: 46px;
    background: var(--brand-yellow);
  }
  .brand-name {
    font-size: 44px;
    font-weight: 700;
    color: var(--ink);
  }
  .swoosh-area { position: absolute; inset: 0; width: 848px; height: 1200px; }
  .mission { position: absolute; inset: 0; font-weight: 400; }
  .line {
    position: absolute;
    line-height: 1;
    white-space: nowrap;
  }
  .to        { left: 93px;  top: 212px; font-size: 77px; letter-spacing: -1px; }
  .provide   { left: 93px;  top: 280px; font-size: 77px; letter-spacing: 0.5px; }
  .the-most  { left: 90px;  top: 353px; font-size: 98px; color: var(--red); letter-spacing: -1px; }
  .hassle    { right: 118px; top: 448px; font-size: 72px; font-weight: 700; font-style: italic; letter-spacing: 1px; }
  .service   { left: 123px; top: 538px; font-size: 50px; font-weight: 700; color: var(--red); letter-spacing: 1px; }
  .whilst    { left: 312px; top: 604px; font-size: 50px; letter-spacing: 4px; }
  .personal  { left: 312px; top: 670px; font-size: 31px; letter-spacing: -0.3px; }
  .people    { left: 96px;  top: 693px; font-size: 106px; color: var(--red); letter-spacing: -2px; }
  .want      { left: 276px; top: 787px; font-size: 105px; letter-spacing: -2px; }
  .tell      { left: 275px; top: 888px; font-size: 34px; letter-spacing: -0.3px; }
</style>
</head>
<body>
<main class="poster">
  <svg class="swoosh-area" viewBox="0 0 848 1200" role="img" aria-label="Decorative swoosh of olive, yellow and orange bands">
    <defs>
      <linearGradient id="swoosh-tones" x1="0" y1="0" x2="0" y2="1">
        <stop offset="0" stop-color="var(--olive)"/>
        <stop offset="0.45" stop-color="var(--gold)"/>
        <stop offset="1" stop-color="var(--orange)"/>
      </linearGradient>
    </defs>
    <path d="M0 790 C150 870 300 1015 560 1058 C700 1080 800 1064 848 1048 L848 1200 L0 1200Z" fill="url(#swoosh-tones)"/>
  </svg>

  <header class="brand">
    <span class="brand-square"></span>
    <span class="brand-name">Kerbside Spaces</span>
  </header>

  <h1 class="mission">
    <span class="line to">To</span>
    <span class="line provide">Provide</span>
    <span class="line the-most">The Most</span>
    <span class="line hassle">Hassle-free</span>
    <span class="line service">Parking Rental Service</span>
    <span class="line whilst">whilst giving a</span>
    <span class="line personal">Personal Customer Experience</span>
    <span class="line people">people</span>
    <span class="line want">want to</span>
    <span class="line tell">Tell Their Friends About</span>
  </h1>
</main>
</body>
</html>
```